A5, portrait
Theme is science
audience is VIPS, politicians, executives
this is a really important event, we want a very classy invitation
include logo for bloom and grow and lantern but lantern one bigger
images attached
Have attached some styles we like but doesn't need to be these colours. If we can incorporate some colours from our logo would be good but don't make too colourful and childish

You’re invited to the official opening and launch of Lantern, Centre of Discovery. an industry first, pioneering, STEM hub.

Saturday 30th April, 2022

10:00 am – 12:00 pm

42 Harlow Lane, Fernwood

Light canapes provided. Dress code is smart/casual

All guests will be given a guided walk through of Australia’s first dedicated STEM education hub for children aged 3-6.

Invitation only

RSVP: 18 April to marketing@bloomandgrow.edu.au

```html
<!DOCTYPE html>
<html lang="en">
<head>
<meta charset="utf-8">
<title>Lantern, Centre of Discovery – Official Opening Invitation</title>
<link rel="stylesheet" href="https://fonts.googleapis.com/css2?family=Playfair+Display:wght@400;700&display=swap">
<style>
  :root {
    --page-bg: #e4e5e8;
    --navy-top: #2d3968;
    --navy-mid: #44557f;
    --navy-bottom: #6483ab;
    --gold: #d2b01c;
    --gold-soft: rgba(210, 176, 28, 0.55);
    --ink: #ffffff;
    --sky: #00aeef;
    --serif: "Playfair Display", Georgia, serif;
  }
  * { box-sizing: border-box; margin: 0; padding: 0; }
  html, body { width: 960px; height: 1200px; overflow: hidden; }
  body { background: var(--page-bg); font-family: var(--serif); color: var(--ink); position: relative; }

  .invitation {
    position: absolute; left: 61px; top: 20px; width: 838px; height: 1160px;
    background: linear-gradient(180deg, var(--navy-top) 0%, var(--navy-mid) 50%, var(--navy-bottom) 100%);
    overflow: hidden;
  }
  .frame {
    position: absolute; left: 43px; top: 43px; width: 752px; height: 1073px;
    border: 1.5px solid var(--gold); border-radius: 33px;
  }
  .rule { position: absolute; left: 148px; width: 542px; height: 0; border-top: 1px solid var(--gold-soft); }
  .rule-top { top: 601px; }
  .rule-mid { top: 706px; }
  .rule-bottom { top: 763px; }

  .text-block { position: absolute; left: 0; width: 100%; text-align: center; }

  .headline { top: 88px; font-size: 46px; font-weight: 700; letter-spacing: 0.5px; line-height: 1; }
  .headline span { display: inline-block; padding-bottom: 6px; border-bottom: 1.5px solid var(--ink); }
  .lead { top: 150px; font-size: 20px; }

  .brand-mark {
    position: absolute; left: 145px; top: 300px; width: 320px; text-align: center;
    font-weight: 400; color: var(--ink);
  }
  .brand-mark .brand-name { font-size: 64px; line-height: 1; letter-spacing: 1px; }
  .brand-mark .brand-tag { font-size: 23px; margin-top: 12px; }

  .venue-photo {
    position: absolute; left: 477px; top: 263px; width: 228px; height: 228px; border-radius: 50%;
    background:
      radial-gradient(circle at 50% 55%, rgba(190, 180, 235, 0.85) 0%, rgba(110, 100, 190, 0.7) 22%, transparent 40%),
      linear-gradient(180deg, #6a5a9c 0%, #3b3e8f 45%, #262a5c 70%, #0e0e14 100%);
  }

  .tagline { top: 554px; font-size: 20px; }

  .details { position: absolute; top: 620px; left: 148px; width: 542px; height: 74px; display: flex; }
  .details .cell { display: flex; flex-direction: column; justify-content: center; align-items: center; font-size: 19.5px; line-height: 27px; }
  .details .date { width: 187px; }
  .details .time { width: 167px; border-left: 1px solid var(--gold-soft); border-right: 1px solid var(--gold-soft); line-height: 19px; }
  .details .place { width: 188px; }

  .extras { position: absolute; top: 716px; left: 148px; width: 542px; height: 38px; display: flex; font-size: 19.5px; }
  .extras .cell { width: 50%; display: flex; align-items: center; justify-content: center; }
  .extras .cell + .cell { border-left: 1px solid var(--gold-soft); padding-left: 20px; }

  .walkthrough { top: 796px; font-size: 19.5px; line-height: 28px; }

  .invite-only {
    position: absolute; left: 324px; top: 876px; width: 190px; height: 41px;
    border: 1px solid var(--gold); border-radius: 21px;
    display: flex; align-items: center; justify-content: center;
    color: var(--gold); font-size: 18.5px; letter-spacing: 0.3px;
  }
  .rsvp { top: 935px; font-size: 19.5px; }
  .rsvp strong { color: var(--gold); font-weight: 700; }

  .partner-tab {
    position: absolute; left: 356px; top: 996px; width: 126px; height: 164px;
    background: var(--sky); border-radius: 10px 10px 0 0;
    display: flex; flex-direction: column; align-items: center; justify-content: center;
    font-size: 21px; font-weight: 700; line-height: 1.15; color: var(--ink); text-align: center;
  }
</style>
</head>
<body>
  <main class="invitation">
    <div class="frame" aria-hidden="true"></div>
    <div class="rule rule-top" aria-hidden="true"></div>
    <div class="rule rule-mid" aria-hidden="true"></div>
    <div class="rule rule-bottom" aria-hidden="true"></div>

    <h1 class="text-block headline"><span>YOU’RE INVITED</span></h1>
    <p class="text-block lead">to the official opening and launch of</p>

    <div class="brand-mark">
      <div class="brand-name">Lantern</div>
      <div class="brand-tag">Centre of Discovery</div>
    </div>

    <div class="venue-photo" role="img" aria-label="Photo of a glowing plasma globe exhibit inside the Lantern STEM hub"></div>

    <p class="text-block tagline">An industry first, pioneering, STEM hub</p>

    <section class="details">
      <div class="cell date"><span>Saturday,</span><span>30th April, 2022</span></div>
      <div class="cell time"><span>10:00 am</span><span>–</span><span>12:00 pm</span></div>
      <div class="cell place"><span>42 Harlow Lane,</span><span>Fernwood</span></div>
    </section>

    <section class="extras">
      <div class="cell">Light canapes provided</div>
      <div class="cell">Dress code is smart/casual</div>
    </section>

    <p class="text-block walkthrough">All guests will be given a guided walk through of Australia’s<br>first dedicated STEM education hub for children aged 3-6.</p>

    <div class="invite-only">INVITATION ONLY</div>

    <p class="text-block rsvp"><strong>RSVP:</strong> 18 April to marketing@bloomandgrow.edu.au</p>

    <div class="partner-tab"><span>Bloom</span><span>and Grow</span></div>
  </main>
</body>
</html>
```